Veltrona Pocket Folder

Create a new pocket folder
An Overview / Background of the Business & Services
We would like a new folder to use when making formal presentations
* The Target Market / Audience you are trying to reach
The target audience are commercial businesses that we are selling group insurance products to
* Design Specifics; any preferences or ideas for Style, Colour, Imagery, etc
We wanted to use the Houston, Texas skyline and create something that was simple, yet modern.
* Do you have an existing website or Facebook page were designers can learn more about your company?
Yes, http://www.veltronagroup.example and we are on Linked-In.
Updates
Project Deadline Extended Reason: We have many people who have to agree. We need to get an answer on the form of the ready art we will receive when we select a designer .Thank you. Added Thursday, April 27, 2017
Industry/Entity Type
Business
Look and feel
Each slider illustrates characteristics of the customer's brand and the style your logo design should communicate.

```html
<!DOCTYPE html>
<html lang="en">
<head>
<meta charset="utf-8">
<title>Veltrona Pocket Folder</title>
<link href="https://fonts.googleapis.com/css2?family=Open+Sans:wght@400;600;700&display=swap" rel="stylesheet">
<style>
  :root {
    --backdrop: #e8e8e8;
    --flap-grey: #6b6c71;
    --flap-text: #c9cacd;
    --blue-deep: #0a72b8;
    --blue-light: #2ea6df;
    --white-panel: #ffffff;
    --panel-shade: #f0f0f0;
    --brand-grey: #5f6266;
    --brand-blue: #1683cc;
    --slit: #ffffff;
    --contact-text: #ffffff;
  }
  html, body {
    margin: 0;
    padding: 0;
    width: 1200px;
    height: 979px;
    overflow: hidden;
    background: var(--backdrop);
    font-family: "Open Sans", Arial, sans-serif;
  }
  .canvas {
    position: relative;
    width: 1200px;
    height: 979px;
  }
  .dieline {
    position: absolute;
    inset: 0;
  }
  .cover-back {
    position: absolute;
    left: 138px; top: 117px;
    width: 448px; height: 563px;
    background: radial-gradient(ellipse at 52% 40%, var(--blue-light) 0%, #1b8fd1 40%, var(--blue-deep) 100%);
  }
  .cover-front {
    position: absolute;
    left: 586px; top: 117px;
    width: 449px; height: 563px;
    background: linear-gradient(200deg, var(--white-panel) 30%, var(--panel-shade) 100%);
  }
  .skyline {
    position: absolute;
    left: 0; right: 0; bottom: 0;
    height: 114px;
  }
  .cover-back .skyline {
    background: linear-gradient(180deg, rgba(10,90,150,0) 0%, rgba(12,96,158,0.55) 35%, rgba(14,100,160,0.75) 100%);
  }
  .cover-front .skyline {
    background: linear-gradient(180deg, rgba(210,214,220,0) 0%, rgba(210,214,220,0.8) 35%, #d4d6da 100%);
  }
  .contact {
    position: absolute;
    left: 28px; bottom: 22px;
    color: var(--contact-text);
    font-size: 8px;
    line-height: 11px;
  }
  .contact .company { font-weight: 700; }
  .contact .line { display: flex; align-items: center; gap: 6px; margin-top: 2px; }
  .contact .address { margin-bottom: 6px; }
  .contact svg { width: 8px; height: 8px; fill: var(--contact-text); }
  .brand {
    position: absolute;
    left: 82px; top: 258px;
    display: flex;
    align-items: center;
    gap: 12px;
  }
  .brand-square {
    width: 52px; height: 52px;
    border-radius: 6px;
    background: var(--brand-blue);
  }
  .brand-name {
    font-weight: 700;
    font-size: 42px;
    letter-spacing: 0.5px;
    color: var(--brand-grey);
  }
  .flap-url {
    position: absolute;
    top: 283px;
    width: 140px;
    font-size: 7px;
    letter-spacing: 1.6px;
    color: var(--flap-text);
    transform: rotate(-90deg);
    transform-origin: center;
    text-align: center;
    white-space: nowrap;
  }
  .flap-url.left { left: 50px; }
  .flap-url.right { left: 983px; }
</style>
</head>
<body>
<div class="canvas">
  <svg class="dieline" width="1200" height="979" viewBox="0 0 1200 979" aria-hidden="true">
    <path d="M104 121 L138 117 L138 680 L104 676 L104 481 A12 12 0 0 0 104 457 Z" fill="var(--flap-grey)"/>
    <path d="M1035 117 L1069 121 L1069 457 A12 12 0 0 0 1069 481 L1069 676 L1035 680 Z" fill="var(--flap-grey)"/>
    <path d="M169 680 L586 680 L555 860 Q550 890 525 890 L169 890 Z" fill="var(--flap-grey)"/>
    <path d="M589 680 L1004 680 L1004 890 L645 890 Q622 890 618 860 Z" fill="var(--flap-grey)"/>
    <g stroke="var(--slit)" stroke-width="1.2">
      <line x1="726" y1="770" x2="754" y2="742"/>
      <line x1="862" y1="742" x2="890" y2="770"/>
      <line x1="726" y1="810" x2="754" y2="838"/>
      <line x1="862" y1="838" x2="890" y2="810"/>
    </g>
  </svg>

  <div class="flap-url left">www.veltronagroup.example</div>
  <div class="flap-url right">www.veltronagroup.example</div>

  <section class="cover-back">
    <div class="skyline" role="img" aria-label="City skyline silhouette in deep blue tones"></div>
    <div class="contact">
      <div class="company">Veltrona Agency LLC</div>
      <div class="address">4200 Westmont Avenue, Suite 310<br>Harlow City, Norland, 00000</div>
      <div class="line">
        <svg viewBox="0 0 24 24"><path d="M6.6 10.8a15 15 0 0 0 6.6 6.6l2.2-2.2a1 1 0 0 1 1-.25 11.4 11.4 0 0 0 3.6.6 1 1 0 0 1 1 1V20a1 1 0 0 1-1 1A17 17 0 0 1 3 4a1 1 0 0 1 1-1h3.5a1 1 0 0 1 1 1c0 1.25.2 2.45.6 3.6a1 1 0 0 1-.25 1z"/></svg>
        <span>555-010-4821</span>
      </div>
      <div class="line">
        <svg viewBox="0 0 24 24"><path d="M2 5h20v14H2z M2 5l10 8 10-8" fill="var(--contact-text)"/></svg>
        <span>info@veltronagroup.example</span>
      </div>
    </div>
  </section>

  <section class="cover-front">
    <div class="brand">
      <div class="brand-square"></div>
      <div class="brand-name">Veltrona</div>
    </div>
    <div class="skyline" role="img" aria-label="City skyline silhouette in pale grey tones"></div>
  </section>
</div>
</body>
</html>
```